Suite Refresh Partners - Tabletop Display

We need a 5'x5' trade show display for a hotel renovation company named "Suite Refresh Partners." Suite Refresh Partners is the most complete authority on hotel renovation in the country, and we're the only 100% turn-key renovator in Colorado. With one phone call, we deliver an approved design, FF&E purchasing, logistics, construction, installation, and warranty administration. The design needs to convey professionalism. Our goal is to help our clients reduce costs and reduce stress while achieving the best results. The colors should align with the attached brochure for our Raleigh office.

Target Market(s)

Hotel owners and general managers

Industry/Entity Type

Design Agency

Colors
3277b5
85acd3
cfdeed

Requirements
Must have
• Our product is a blend of design and construction. I need to convey our services and attention to detail without seeming salesy, bold, or aggressive. The goal is to convey confidence and help to relax our potential client base.
Nice to have
• Possibly one or more photos of completed projects. Not sure if exterior, lobby, or guest room photos would be best. I can send files via dropbox if that's helpful.
Should not have
• I've included a photo of the old display at a trade show. I strongly dislike the yellow and red on the display. Please try to stick to the color palette of the attached brochure.

```html
<!DOCTYPE html>
<html lang="en">
<head>
<meta charset="utf-8">
<title>Suite Refresh Partners – Tabletop Display</title>
<link rel="stylesheet" href="https://fonts.googleapis.com/css2?family=Bebas+Neue&family=Open+Sans:wght@400;600;700&display=swap">
<style>
  :root {
    --brand-blue: #225e9f;
    --charcoal: #555555;
    --headline: #444444;
    --paper: #ededed;
    --white: #ffffff;
  }
  html, body {
    margin: 0;
    padding: 0;
    width: 1135px;
    height: 1200px;
    overflow: hidden;
    background: var(--paper);
  }
  .display {
    position: relative;
    width: 1135px;
    height: 1200px;
    font-family: "Open Sans", Arial, sans-serif;
  }
  .display__art {
    position: absolute;
    inset: 0;
  }
  .brand {
    position: absolute;
    left: 890px;
    top: 60px;
    width: 210px;
    color: var(--brand-blue);
    font-weight: 700;
    font-size: 27px;
    line-height: 1.15;
    text-align: center;
  }
  .headline {
    position: absolute;
    left: 0;
    top: 596px;
    width: 1135px;
    margin: 0;
    text-align: center;
    font-family: "Bebas Neue", "Arial Narrow", sans-serif;
    font-weight: 400;
    font-size: 70px;
    line-height: 1;
    color: var(--headline);
  }
  .services {
    position: absolute;
    left: 38px;
    top: 966px;
    color: var(--white);
  }
  .services__title {
    margin: 0 0 8px;
    font-weight: 700;
    font-size: 29px;
    line-height: 1.1;
  }
  .services__list {
    display: grid;
    grid-template-columns: 202px auto;
    grid-auto-flow: column;
    grid-template-rows: repeat(4, 39px);
    margin: 0;
    padding: 0;
    list-style: none;
    font-size: 25px;
  }
  .services__item::before {
    content: "\2713";
    margin-right: 12px;
  }
  .contact {
    position: absolute;
    left: 678px;
    top: 964px;
    color: var(--white);
  }
  .contact__title {
    margin: 0 0 6px;
    font-weight: 700;
    font-size: 39px;
    line-height: 1;
  }
  .contact__phone {
    margin: 0;
    font-weight: 700;
    font-size: 52px;
    line-height: 1.12;
  }
  .contact__web {
    margin: 6px 0 0;
    font-size: 24px;
  }
</style>
</head>
<body>
<main class="display">
  <svg class="display__art" viewBox="0 0 1135 1200" width="1135" height="1200" aria-hidden="false">
    <defs>
      <linearGradient id="exterior-tones" x1="0" y1="0" x2="0" y2="1">
        <stop offset="0" stop-color="#7fb6e6"/>
        <stop offset="0.45" stop-color="#c2ad8f"/>
        <stop offset="1" stop-color="#4d7d3a"/>
      </linearGradient>
      <linearGradient id="lobby-green" x1="0" y1="0" x2="0" y2="1">
        <stop offset="0" stop-color="#d9d7b8"/>
        <stop offset="1" stop-color="#5b4a3a"/>
      </linearGradient>
      <linearGradient id="lobby-red" x1="0" y1="0" x2="0" y2="1">
        <stop offset="0" stop-color="#4a3a30"/>
        <stop offset="1" stop-color="#a8452c"/>
      </linearGradient>
      <linearGradient id="lobby-warm" x1="0" y1="0" x2="0" y2="1">
        <stop offset="0" stop-color="#c89a63"/>
        <stop offset="1" stop-color="#7a3b28"/>
      </linearGradient>
    </defs>

    <!-- hero photo area -->
    <polygon class="hero-photo" role="img" aria-label="Photo of a renovated two-storey house with landscaped front garden"
      points="0,0 1135,0 1135,299 583,539 476,466 0,208" fill="url(#exterior-tones)"/>
    <polygon points="0,208 476,466 0,483" fill="var(--brand-blue)"/>
    <polygon points="296,473 476,469 630,580" fill="var(--charcoal)"/>
    <polygon points="583,539 1135,299 1135,453 630,580" fill="var(--brand-blue)"/>

    <!-- brand box -->
    <polygon points="872,0 1114,0 1114,221 872,252" fill="var(--white)"/>

    <!-- project photos -->
    <polygon role="img" aria-label="Photo of a renovated hotel lobby with green walls and lime seating"
      points="163,687 423,687 375,902 115,902" fill="url(#lobby-green)" stroke="var(--brand-blue)" stroke-width="3"/>
    <polygon role="img" aria-label="Photo of a renovated hotel lounge with red carpet and sofas"
      points="455,687 716,687 670,902 408,902" fill="url(#lobby-red)" stroke="var(--brand-blue)" stroke-width="3"/>
    <polygon role="img" aria-label="Photo of a renovated hotel lobby with orange armchairs"
      points="748,687 1010,687 963,902 702,902" fill="url(#lobby-warm)" stroke="var(--brand-blue)" stroke-width="3"/>

    <!-- footer bands -->
    <polygon points="0,935 505,935 510,949 0,949" fill="var(--charcoal)"/>
    <polygon points="512,935 1135,935 1135,949 517,949" fill="var(--brand-blue)"/>
    <polygon points="0,955 508,955 618,1200 0,1200" fill="var(--brand-blue)"/>
    <polygon points="522,955 1135,955 1135,1200 632,1200" fill="var(--charcoal)"/>
  </svg>

  <div class="brand">Suite Refresh<br>Partners</div>

  <h1 class="headline">A Complete Renovation With Just One Call!</h1>

  <section class="services">
    <h2 class="services__title">WE DELIVER</h2>
    <ul class="services__list">
      <li class="services__item">Design</li>
      <li class="services__item">Planning</li>
      <li class="services__item">Installation</li>
      <li class="services__item">Construction</li>
      <li class="services__item">FF&amp;E</li>
      <li class="services__item">Logistics</li>
      <li class="services__item">Specification</li>
      <li class="services__item">Warranty Administration</li>
    </ul>
  </section>

  <section class="contact">
    <h2 class="contact__title">CALL US</h2>
    <p class="contact__phone">555-014-2738</p>
    <p class="contact__phone">555-018-6190</p>
    <p class="contact__web">www.suiterefreshpartners.com</p>
  </section>
</main>
</body>
</html>
```